Quarrybend Marble & Tile Needs a Business Card

Attached you will find your logo, my photo and design guidelines for a new business card. The final design will need two separate files to create an embossed card. The cards will be printed by www.plinkprint.com (Instructions below)
Format is the Plink SQUARE card
Quarrybend Marble And Tile is a brick and mortar, retail stone and tile shop.
One the front:
Quarrybend Marble And Tile
Dorian Fesslock
Owner
24807 Hollis Verdant Blvd
Suite P & R
Charlotte, NC 28193
Cell: 704-583-7142
Web: www.QuarrybendMarbleAndTile.com
(Make each word of the domain a different or alternating color)
On the back;
Something that shows beautiful colorful tile
Follow the design guide closely please. For more information see this page that describes creating the spot gloss file: https://www.plinkprint.com/us/business-cards/design-guidelines-spot-gloss
The logo is what we would like to have raised spot glossed.
Format is the Plink SQUARE card. See attahced guidlines.

```html
<!DOCTYPE html>
<html lang="en">
<head>
<meta charset="utf-8">
<title>Quarrybend Marble &amp; Tile — Business Card</title>
<link href="https://fonts.googleapis.com/css2?family=Libre+Baskerville&family=Montserrat:wght@400;500&display=swap" rel="stylesheet">
<style>
  :root {
    --backdrop: #7a7b7e;
    --card-dark: #243340;
    --card-light: #ffffff;
    --ink: #1c2530;
    --mark-on-dark: #7f93a5;
    --rust: #8f3a17;
    --amber: #c07a1f;
    --slate: #5d6670;
    --photo-tone: #3a3d42;
    --deco-peach: #ecd3c2;
    --deco-grey: #c9c8cd;
    --deco-cream: #f2e3cc;
  }
  * { box-sizing: border-box; margin: 0; padding: 0; }
  html, body { width: 900px; height: 1200px; overflow: hidden; }
  body {
    background: var(--backdrop);
    position: relative;
    font-family: "Montserrat", sans-serif;
    color: var(--ink);
  }
  .card {
    position: absolute;
    left: 134px;
    width: 632px;
    height: 364px;
    overflow: hidden;
  }
  .card--front { top: 210px; background: var(--card-dark); }
  .card--back { top: 626px; background: var(--card-light); }

  .wordmark {
    position: absolute;
    display: flex;
    align-items: center;
    font-family: "Libre Baskerville", serif;
    font-weight: 400;
  }
  .wordmark__square { flex: none; }
  .wordmark__name { display: flex; flex-direction: column; line-height: 1; }
  .wordmark__top { letter-spacing: 0.08em; }
  .wordmark__sub { letter-spacing: 0.42em; }

  .card--front .wordmark { left: 150px; top: 140px; gap: 22px; color: var(--mark-on-dark); }
  .card--front .wordmark__square { width: 18px; height: 18px; background: var(--mark-on-dark); }
  .card--front .wordmark__top { font-size: 38px; }
  .card--front .wordmark__sub { font-size: 15px; margin-top: 14px; }

  .card--back .wordmark { left: 296px; top: 48px; gap: 14px; color: var(--ink); }
  .card--back .wordmark__square { width: 14px; height: 14px; background: var(--ink); }
  .card--back .wordmark__top { font-size: 28px; }
  .card--back .wordmark__sub { font-size: 11px; margin-top: 10px; }

  .portrait {
    position: absolute;
    left: 29px; top: 31px;
    width: 90px; height: 90px;
    background: var(--photo-tone);
    border: 2px solid var(--amber);
  }
  .person { position: absolute; left: 31px; top: 141px; }
  .person__name {
    font-family: "Libre Baskerville", serif;
    font-size: 23px;
    color: var(--ink);
  }
  .person__role { font-size: 14px; color: var(--rust); margin-top: 2px; }
  .divider {
    position: absolute;
    left: 31px; top: 195px;
    width: 190px; height: 3px;
    background: linear-gradient(90deg, var(--rust), var(--slate), var(--rust), var(--slate));
  }
  .contact { position: absolute; left: 31px; top: 210px; font-size: 14.5px; }
  .contact__line { height: 25px; line-height: 25px; }
  .contact__phone, .contact__web {
    display: flex; align-items: center; gap: 6px; line-height: 25px;
  }
  .contact__phone { margin-top: 3px; letter-spacing: 0.16em; font-size: 15px; font-weight: 500; }
  .contact__web { font-size: 15px; }
  .icon { width: 15px; height: 15px; flex: none; }
  .web-quarry { color: var(--rust); }
  .web-marble { color: var(--amber); }
  .web-and { color: var(--rust); }
  .web-tile { color: var(--slate); }

  .tile-decoration {
    position: absolute;
    left: 376px; top: 108px;
    width: 300px; height: 300px;
    background:
      radial-gradient(circle at 50% 50%, var(--deco-grey) 0%, rgba(201,200,205,0.6) 35%, rgba(255,255,255,0) 72%),
      linear-gradient(135deg, var(--deco-peach) 0%, rgba(255,255,255,0) 45%, var(--deco-cream) 100%);
    opacity: 0.85;
  }
</style>
</head>
<body>
  <section class="card card--front" aria-label="Card front">
    <div class="wordmark">
      <span class="wordmark__square"></span>
      <div class="wordmark__name">
        <span class="wordmark__top">QUARRYBEND</span>
        <span class="wordmark__sub">MARBLE &amp; TILE</span>
      </div>
    </div>
  </section>

  <section class="card card--back" aria-label="Card back">
    <div class="portrait" role="img" aria-label="Portrait photo of the owner"></div>

    <div class="wordmark">
      <span class="wordmark__square"></span>
      <div class="wordmark__name">
        <span class="wordmark__top">QUARRYBEND</span>
        <span class="wordmark__sub">MARBLE &amp; TILE</span>
      </div>
    </div>

    <div class="person">
      <p class="person__name">Dorian Fesslock</p>
      <p class="person__role">Owner</p>
    </div>
    <div class="divider" role="img" aria-label="Decorative tile border strip"></div>

    <div class="contact">
      <p class="contact__line">24807 Hollis Verdant Blvd</p>
      <p class="contact__line">Suite P &amp; R</p>
      <p class="contact__line">Charlotte, NC 28193</p>
      <p class="contact__phone">
        <svg class="icon" viewBox="0 0 24 24" aria-hidden="true"><path fill="#8f3a17" d="M6.6 10.8a15.1 15.1 0 0 0 6.6 6.6l2.2-2.2c.3-.3.7-.4 1-.2 1.1.4 2.3.6 3.6.6.6 0 1 .4 1 1V20c0 .6-.4 1-1 1A17 17 0 0 1 3 4c0-.6.4-1 1-1h3.5c.6 0 1 .4 1 1 0 1.3.2 2.5.6 3.6.1.3 0 .7-.2 1z"/></svg>
        704-583-7142
      </p>
      <p class="contact__web">
        <svg class="icon" viewBox="0 0 24 24" aria-hidden="true" fill="none" stroke="#8f3a17" stroke-width="2"><circle cx="12" cy="12" r="9"/><path d="M3 12h18M12 3c3 3 3 15 0 18M12 3c-3 3-3 15 0 18"/></svg>
        <span>www.<span class="web-quarry">Quarrybend</span><span class="web-marble">Marble</span><span class="web-and">And</span><span class="web-tile">Tile</span>.com</span>
      </p>
    </div>

    <div class="tile-decoration" role="img" aria-label="Faint decorative pattern of colourful tile"></div>
  </section>
</body>
</html>
```